Business Card Design Competition

We need a business card design for our Internet Marketing company. We require both front and back designs and the final card must be 89x53mm in size, plus crop marks to 91x55mm. Colours as per logo, plus perhaps black and/or grey (#828282).
Final text must be editable (if you can supply an editable Fireworks PNG, even better)...
FRONT TEXT:
Full Name
Position
Address Line
Suburb, State, Postcode
Phone: 0000 000 000
Mobile: 0000 000 000
Email: xxx@brightlanemedia.com.au
Web: www.brightlanemedia.com.au
Rear of card should be a fresh design plus our slogan text: "Making You Visible" in large font, then in small text "Kestrel Holdings Pty Ltd (ABN: 42 561 903 774)".
Target Market(s)
Small/Medium Businesses
Industry/Entity Type
Business

```html
<!DOCTYPE html>
<html lang="en">
<head>
<meta charset="utf-8">
<title>Brightlane Media – Business Cards</title>
<link href="https://fonts.googleapis.com/css2?family=Open+Sans:wght@400;600;700&display=swap" rel="stylesheet">
<style>
  :root {
    --page-bg: #e9e6e1;
    --card-bg: #2b2a2b;
    --white: #ffffff;
    --soft-white: #e6e6e6;
    --orange: #f5a031;
    --green: #8cc63f;
  }
  * { margin: 0; padding: 0; box-sizing: border-box; }
  html, body { width: 1200px; height: 900px; overflow: hidden; }
  body {
    background: var(--page-bg);
    font-family: "Open Sans", Arial, sans-serif;
    position: relative;
  }
  .card {
    position: absolute;
    top: 292px;
    width: 546px;
    height: 310px;
    background: var(--card-bg);
    border-radius: 20px;
    overflow: hidden;
    color: var(--white);
  }
  .card--front { left: 37px; }
  .card--back { left: 620px; }

  .holder { position: absolute; left: 45px; top: 84px; }
  .holder__name { font-size: 20px; font-weight: 700; line-height: 1.1; }
  .holder__role { font-size: 12px; color: var(--soft-white); }

  .address {
    position: absolute; left: 45px; top: 140px;
    font-size: 11.5px; line-height: 18px; color: var(--soft-white);
  }
  .contact-list {
    position: absolute; left: 30px; list-style: none;
    font-size: 11.5px; line-height: 18px; color: var(--soft-white);
  }
  .contact-list--phone { top: 185px; }
  .contact-list--online { top: 229px; }
  .contact-list li { display: flex; align-items: center; gap: 8px; }
  .contact-list svg { width: 11px; height: 11px; flex: none; }

  .brand-front {
    position: absolute; left: 272px; top: 116px;
    display: flex; align-items: center; gap: 8px;
  }
  .brand-front__dot {
    width: 56px; height: 56px; border-radius: 50%; background: var(--green);
  }
  .brand-front__name {
    font-size: 22px; font-weight: 600; color: var(--orange); line-height: 1.05;
  }

  .back-sphere {
    position: absolute; left: -120px; top: -5px;
    width: 320px; height: 320px; border-radius: 50%;
    background: var(--green);
  }
  .brand-back {
    position: absolute; right: 60px; top: 98px;
    font-size: 40px; font-weight: 600; color: var(--orange); line-height: 1.05;
    text-align: right;
  }
  .slogan {
    position: absolute; right: 68px; top: 188px;
    font-size: 26px; font-weight: 400; color: var(--white);
  }
  .legal {
    position: absolute; right: 52px; top: 280px;
    font-size: 11.5px; color: var(--white);
  }
</style>
</head>
<body>
  <section class="card card--front">
    <div class="holder">
      <p class="holder__name">Thomas Avery</p>
      <p class="holder__role">Company Director</p>
    </div>
    <p class="address">18 harbour view road, Kellsbridge<br>County Ardmore KB17 4LT 5678</p>
    <ul class="contact-list contact-list--phone">
      <li>
        <svg viewBox="0 0 12 12" aria-hidden="true"><rect x="3" y="0.5" width="6" height="11" rx="1" fill="var(--orange)"/><rect x="4" y="2" width="4" height="6" fill="var(--card-bg)"/></svg>
        061-555-0182
      </li>
      <li>
        <svg viewBox="0 0 12 12" aria-hidden="true"><path d="M1 4 Q6 0 11 4 L10 6 L8 5 L8 4 Q6 3 4 4 L4 5 L2 6 Z" fill="var(--orange)"/><rect x="2" y="6.5" width="8" height="4.5" rx="1" fill="var(--orange)"/></svg>
        061-555-0147
      </li>
    </ul>
    <ul class="contact-list contact-list--online">
      <li>
        <svg viewBox="0 0 12 12" aria-hidden="true"><rect x="0.8" y="2.3" width="10.4" height="7.4" fill="none" stroke="var(--orange)" stroke-width="1.3"/><path d="M1 2.6 L6 6.5 L11 2.6" fill="none" stroke="var(--orange)" stroke-width="1.2"/></svg>
        thomas@brightlanemedia.com.au
      </li>
      <li>
        <svg viewBox="0 0 12 12" aria-hidden="true"><circle cx="6" cy="6" r="5" fill="none" stroke="var(--orange)" stroke-width="1.3"/><ellipse cx="6" cy="6" rx="2.2" ry="5" fill="none" stroke="var(--orange)" stroke-width="1"/><line x1="1" y1="6" x2="11" y2="6" stroke="var(--orange)" stroke-width="1"/></svg>
        brightlanemedia.com.au
      </li>
    </ul>
    <div class="brand-front">
      <span class="brand-front__dot"></span>
      <span class="brand-front__name">Brightlane<br>Media</span>
    </div>
  </section>

  <section class="card card--back">
    <div class="back-sphere"></div>
    <p class="brand-back">Brightlane<br>Media</p>
    <p class="slogan">Making You Visible</p>
    <p class="legal">Kestrel Holdings Pty Ltd (ABN: 42 561 903 774)</p>
  </section>
</body>
</html>
```